Awesome photographers card for an awesome new business

Double sided business card Black background and silver logo in middle on one side. Details on otherside. please keep it simple

Industry/Entity Type

Photographer

Contact Information for Business Card

Gerald Fenwick
0452817360
GeraldFenwickPhotography47@mailbox.test
www.GeraldFenwickPhotography.test.au
Instagram _Gerald_fenwick

Requirements
Must have
• My logo in Silver
• please use instagram logo instead of "Instagram"

```html
<!DOCTYPE html>
<html lang="en">
<head>
<meta charset="utf-8">
<title>Gerald Fenwick Photography – Business Card</title>
<link href="https://fonts.googleapis.com/css2?family=Roboto:wght@400;500&family=Roboto+Condensed:wght@500&display=swap" rel="stylesheet">
<style>
  :root {
    --stage: #e9e4dc;
    --card-front: #f7f7f7;
    --card-back: #1c1d1f;
    --silver: #9a9a9a;
    --silver-light: #d4d4d4;
    --ink-grey: #4a4a4a;
    --rule: #55575a;
    --text-light: #f2f2f2;
    --name-grey: #cfcfcf;
  }
  * { margin: 0; padding: 0; box-sizing: border-box; }
  html, body {
    width: 1200px; height: 960px; overflow: hidden;
    background: var(--stage);
    font-family: "Roboto", Arial, sans-serif;
  }
  .canvas { position: relative; width: 1200px; height: 960px; }

  .card {
    position: absolute; left: 320px; width: 600px;
    border-radius: 16px; overflow: hidden;
  }
  .card--front {
    top: 95px; height: 355px; background: var(--card-front);
    box-shadow: 0 2px 4px rgba(0,0,0,.18);
  }
  .card--back {
    top: 493px; height: 343px; background: var(--card-back);
    box-shadow: 0 2px 4px rgba(0,0,0,.3);
  }

  .front-brand {
    position: absolute; top: 160px; left: 0; width: 100%;
    text-align: center; font-size: 44px; font-weight: 400;
    color: var(--silver); letter-spacing: 1px;
  }
  .front-web {
    position: absolute; top: 303px; left: 0; width: 100%;
    text-align: center; font-size: 15px; letter-spacing: 2.2px;
    color: var(--ink-grey);
  }

  .back-brand {
    position: absolute; top: 86px; left: 412px;
    display: flex; align-items: center; gap: 8px;
  }
  .back-brand__circle {
    width: 14px; height: 14px; border-radius: 50%;
    border: 2px solid var(--silver-light);
  }
  .back-brand__name {
    font-size: 15px; color: var(--silver-light); font-weight: 400;
  }

  .holder-name {
    position: absolute; top: 192px; left: 36px;
    font-family: "Roboto Condensed", "Arial Narrow", sans-serif;
    font-weight: 500; font-size: 22px; color: var(--name-grey);
    letter-spacing: .3px;
  }
  .holder-rule {
    position: absolute; top: 224px; left: 36px; width: 528px;
    height: 1px; background: var(--rule);
  }
  .contact-list {
    position: absolute; top: 235px; left: 36px; list-style: none;
  }
  .contact-list li {
    display: flex; align-items: center; height: 19.3px;
    font-size: 14.5px; color: var(--text-light);
  }
  .contact-list svg { width: 13px; height: 13px; margin-right: 12px; fill: var(--text-light); }

  .silver-band {
    position: absolute; left: 0; bottom: 0; width: 100%; height: 11px;
    background: linear-gradient(90deg, #6e6e6e 0%, #d9d9d9 45%, #9c9c9c 64%);
  }
  .silver-band__split {
    position: absolute; left: 392px; bottom: 0; width: 208px; height: 11px;
    background: linear-gradient(90deg, #b9b9b9, #e3e3e3);
    border-left: 3px solid var(--card-back);
  }
</style>
</head>
<body>
<main class="canvas">
  <section class="card card--front" aria-label="Card front">
    <div class="front-brand">Gerald Fenwick</div>
    <div class="front-web">www.GeraldFenwickPhotography.test.au</div>
  </section>

  <section class="card card--back" aria-label="Card back">
    <div class="back-brand">
      <span class="back-brand__circle"></span>
      <span class="back-brand__name">Gerald Fenwick</span>
    </div>
    <h1 class="holder-name">GERALD FENWICK</h1>
    <div class="holder-rule"></div>
    <ul class="contact-list">
      <li><svg viewBox="0 0 24 24"><path d="M6.6 10.8a15 15 0 0 0 6.6 6.6l2.2-2.2a1 1 0 0 1 1-.25 11.4 11.4 0 0 0 3.6.57 1 1 0 0 1 1 1V20a1 1 0 0 1-1 1A17 17 0 0 1 3 4a1 1 0 0 1 1-1h3.5a1 1 0 0 1 1 1c0 1.25.2 2.45.57 3.57a1 1 0 0 1-.25 1z"/></svg>0452817360</li>
      <li><svg viewBox="0 0 24 24"><path d="M2 5h20v14H2z M4 7v.5l8 5 8-5V7l-8 5z" fill-rule="evenodd"/></svg>GeraldFenwickPhotography47@mailbox.test</li>
      <li><svg viewBox="0 0 24 24"><circle cx="12" cy="12" r="10"/><path d="M2 12h20M12 2c3 3 3 17 0 20M12 2c-3 3-3 17 0 20" stroke="#1c1d1f" stroke-width="1.6" fill="none"/></svg>www.GeraldFenwickPhotography.test.au</li>
      <li><svg viewBox="0 0 24 24"><rect x="2" y="2" width="20" height="20" rx="2"/></svg>Gerald_fenwick</li>
    </ul>
    <div class="silver-band"><div class="silver-band__split"></div></div>
  </section>
</main>
</body>
</html>
```